I need a logo that demonstrates multiple of the same with one of a distinguishing feature. I would like something that can be recognisable in silhouette format. The business designs Management systems bespoke the to the company helping them pre-qualify for work.
Something that can demonstrate a distinction between a collective group non of which are the same in shape or size, with the largest of these not the distinguished object (or something to that effect).
This is a new business no logo or artwork exists.
Target Market(s)
Small to Medium Size enterprises in the city and rural areas. Looking to make the step up.
Industry/Entity Type
Manufacture
Contact Information for Business Card
room for, Name, Email, phone number
Font styles to use
Requirements
Must have
- would like the silhouette to be recognisable
Nice to have
- would like it to incorporate the name Keystone Advisory Frameworks.
- Would like the same logo to be on both business cards and on corporate shirts
Should not have
- anything that may exclude rural trade or manufacturing.
- I don't want to appear as corporate, just professional

```html
<!DOCTYPE html>
<html lang="en">
<head>
<meta charset="utf-8">
<title>Keystone Advisory Frameworks – Business Card</title>
<link rel="stylesheet" href="https://fonts.googleapis.com/css2?family=Open+Sans:wght@400;600&display=swap">
<style>
  :root {
    --stage: #000000;
    --card-light: #f3f3f3;
    --brand-orange: #f07126;
    --text-grey: #3d3d3d;
    --white: #ffffff;
  }
  * { box-sizing: border-box; margin: 0; padding: 0; }
  html, body {
    width: 1200px;
    height: 900px;
    overflow: hidden;
    background: var(--stage);
    font-family: "Open Sans", Arial, sans-serif;
  }
  .canvas {
    position: relative;
    width: 1200px;
    height: 900px;
  }
  .card {
    position: absolute;
    top: 200px;
    width: 310px;
    height: 502px;
  }
  .card--front {
    left: 265px;
    background: var(--card-light);
    border-radius: 62px 0 62px 0;
  }
  .card--back {
    left: 641px;
    width: 309px;
    background: var(--brand-orange);
    border-radius: 0 62px 0 62px;
  }
  .brand-dot {
    position: absolute;
    left: 110px;
    top: 40px;
    width: 90px;
    height: 90px;
    border-radius: 50%;
    background: var(--brand-orange);
  }
  .wordmark {
    position: absolute;
    font-family: "Open Sans", Arial, sans-serif;
    font-weight: 400;
    line-height: 1;
  }
  .wordmark__main {
    display: block;
    font-size: 35px;
    letter-spacing: 0.5px;
  }
  .wordmark__sub {
    display: block;
    font-size: 17px;
    letter-spacing: 1.2px;
    margin-top: 2px;
  }
  .card--front .wordmark {
    left: 28px;
    top: 173px;
    color: var(--brand-orange);
  }
  .card--back .wordmark {
    left: 34px;
    top: 396px;
    color: var(--white);
  }
  .contact {
    position: absolute;
    left: 27px;
    top: 328px;
    color: var(--text-grey);
    font-size: 13.5px;
    line-height: 1.15;
  }
  .contact__name {
    color: var(--brand-orange);
    font-weight: 600;
    font-size: 17px;
    margin-bottom: 5px;
  }
  .contact__role { margin-bottom: 19px; }
  .contact__address { margin-bottom: 12px; }
  .contact__line {
    display: flex;
    align-items: center;
    gap: 7px;
    margin-bottom: 4px;
  }
  .contact__icon { width: 10px; height: 10px; flex: none; }
</style>
</head>
<body>
<main class="canvas">
  <section class="card card--front" aria-label="Business card front">
    <span class="brand-dot" aria-hidden="true"></span>
    <h1 class="wordmark">
      <span class="wordmark__main">KEYSTONE</span>
      <span class="wordmark__sub">Advisory Frameworks</span>
    </h1>
    <div class="contact">
      <p class="contact__name">MARTIN HALE</p>
      <p class="contact__role">Managing Director</p>
      <p class="contact__address">1234, Address Goes Here<br>Country Name, 123456</p>
      <p class="contact__line">
        <svg class="contact__icon" viewBox="0 0 10 10" aria-hidden="true">
          <path d="M1 3 Q5 0 9 3 L8 4.5 L6.5 3.8 L6.5 3 Q5 2.5 3.5 3 L3.5 3.8 L2 4.5 Z M2.5 5 L7.5 5 L8.5 9 L1.5 9 Z" fill="var(--brand-orange)"/>
        </svg>
        <span>823-456-7890</span>
      </p>
      <p class="contact__line">
        <svg class="contact__icon" viewBox="0 0 10 10" aria-hidden="true">
          <rect x="0.5" y="2" width="9" height="6.5" fill="var(--brand-orange)"/>
          <path d="M0.8 2.3 L5 5.6 L9.2 2.3" stroke="var(--card-light)" stroke-width="0.9" fill="none"/>
        </svg>
        <span>info@youremail.com</span>
      </p>
    </div>
  </section>

  <section class="card card--back" aria-label="Business card back">
    <h2 class="wordmark">
      <span class="wordmark__main">KEYSTONE</span>
      <span class="wordmark__sub">Advisory Frameworks</span>
    </h2>
  </section>
</main>
</body>
</html>
```